Covid 19 Exit Strategy one page brochure

I would like to design, and will need URGENT help, a brochure detailing a Covid 19 Exit Strategy plan. This brochure will need to be understood easily and the graphics inside should make it easy for people to understand without reading the entire text. This project is quite urgent and needs to be completed THIS WEEK - by Saturday may 16th at the latest. I am attaching two examples. I will provide the text.

```html
<!DOCTYPE html>
<html lang="en">
<head>
<meta charset="utf-8">
<title>COVID-19 Phased Exit Strategy</title>
<link href="https://fonts.googleapis.com/css2?family=Exo+2:wght@500;700;800&family=PT+Sans:wght@400;700&display=swap" rel="stylesheet">
<style>
  :root{
    --stage:#8a8a8a;
    --paper:#ffffff;
    --red:#e8202f;
    --navy:#0f2a5a;
    --deep:#0a1f45;
    --blue:#2a9ad8;
    --icon-bg:#e2f0fa;
    --ink:#222428;
  }
  *{margin:0;padding:0;box-sizing:border-box}
  html,body{width:1200px;height:1200px;overflow:hidden;background:var(--stage)}
  .canvas{position:relative;width:1200px;height:1200px;overflow:hidden}
  .brochure{
    position:absolute;left:345px;top:71px;width:823px;height:1703px;
    background:var(--paper);transform:scale(0.621);transform-origin:0 0;
    font-family:"PT Sans",sans-serif;color:var(--ink);
  }
  .hero{
    position:absolute;left:0;top:0;width:823px;height:190px;
    background:radial-gradient(ellipse at 50% 60%,#1f5fa8 0%,#123f7c 45%,var(--deep) 100%);
    text-align:center;
  }
  .hero-title{position:absolute;left:0;right:0;top:32px;font-family:"Exo 2",sans-serif;font-weight:800;font-size:40px;line-height:46px;color:#fff;letter-spacing:.5px}
  .hero-sub{position:absolute;left:0;right:0;top:80px;font-family:"Exo 2",sans-serif;font-weight:800;font-size:40px;line-height:46px;color:var(--red)}
  .hero-credit{position:absolute;left:0;right:0;top:126px;font-family:"Exo 2",sans-serif;font-weight:500;font-size:31px;line-height:38px;color:#fff}
  .intro{position:absolute;left:38px;top:202px;width:747px;font-size:10.8px;line-height:14.6px;text-align:justify;letter-spacing:-.25px}
  .tag{position:absolute;left:290px;top:288px;width:242px;height:26px;background:var(--red);color:#fff;font-family:"Exo 2",sans-serif;font-weight:700;font-size:17px;text-align:center;line-height:26px}
  .req{position:absolute;width:240px}
  .req-icon{position:absolute;left:0;top:0;width:54px;height:54px;border-radius:50%;background:var(--blue)}
  .req-num{position:absolute;left:-4px;top:-2px;width:17px;height:17px;border-radius:50%;background:var(--red);color:#fff;font-size:11px;font-weight:700;text-align:center;line-height:17px}
  .req-text{position:absolute;left:62px;top:0;width:164px;font-size:11px;line-height:14.6px;text-align:justify;letter-spacing:-.15px}
  .req-text.tight{font-size:9.8px;line-height:13.6px;letter-spacing:-.25px;width:174px}
  .plan-band{position:absolute;left:38px;top:594px;width:747px;height:47px;background:var(--red);color:#fff;font-family:"Exo 2",sans-serif;font-weight:800;font-size:25px;text-align:center;line-height:47px}
  .plan-lead{position:absolute;left:40px;top:650px;width:743px;text-align:center;font-size:12.5px;line-height:16px}
  .plan-lead strong{display:block;margin-top:7px;font-size:12px}
  .plan-box{position:absolute;left:48px;top:722px;width:726px;height:891px;border:2px solid var(--navy)}
  .step{position:absolute}
  .step-icon{position:absolute;left:0;top:0;width:64px;height:64px;border-radius:8px;background:var(--icon-bg)}
  .step-text{position:absolute;top:4px;font-size:11.8px;line-height:15.4px;text-align:justify;letter-spacing:-.15px}
  .left{left:26px}.left .step-text{left:102px;width:208px}
  .right{left:397px}.right .step-text{left:86px;width:210px}
  .transport .step-text{left:90px;width:576px}
  .footer-band{position:absolute;left:0;top:1633px;width:823px;height:48px;background:var(--red);color:#fff;font-family:"Exo 2",sans-serif;font-weight:500;font-size:22px;text-align:center;line-height:48px;word-spacing:2px}
</style>
</head>
<body>
<div class="canvas">
  <article class="brochure">
    <header class="hero" role="img" aria-label="Dark blue background of magnified virus particles">
      <h1 class="hero-title">COVID-19</h1>
      <h2 class="hero-sub">PHASED EXIT STRATEGY</h2>
      <p class="hero-credit">Developed by Lena Varga</p>
    </header>

    <p class="intro">Pandemics have, historically, seen their end both medically - via herd immunity or immunizations. And while there are several clinical trials underway for potential Covid-19 vaccines, we are still a long way from deploying an effective vaccine and one that will stand the test of time as the virus changes. Covid-19 pandemic will be considered 'ended' when there are only occasional traces of localized cases that are quickly contained in specific locations., Today and in the absence of an effective vaccine(s) and for the re-opening of the economies and social activities to be successful, it is critical that the following basic conditions be in place before any lockdowns are lifted and before social activities resume:</p>

    <div class="tag">GENERAL REQUIREMENTS</div>

    <div class="req" style="left:44px;top:335px"><div class="req-icon" role="img" aria-label="Case report icon"></div><span class="req-num">1</span><p class="req-text">Single digit downward trend of documented cases within the past 14- days.</p></div>
    <div class="req" style="left:44px;top:405px"><div class="req-icon" role="img" aria-label="Hospital icon"></div><span class="req-num">2</span><p class="req-text">Hospitals and the health care system are capable of treating patients without operating on a crisis mode.</p></div>
    <div class="req" style="left:44px;top:474px"><div class="req-icon" role="img" aria-label="Test tube icon"></div><span class="req-num">3</span><p class="req-text">Ability to screen and test symptomatic individuals within 24 hours of identification. Increased and sufficient testing capacity, to test at least 50% of all population if necessary within a timeframe of 3 months.</p></div>

    <div class="req" style="left:294px;top:335px"><div class="req-icon" role="img" aria-label="ICU bed icon"></div><span class="req-num">4</span><p class="req-text">Ability to surge ICU capacity on a short notice - 24h.</p></div>
    <div class="req" style="left:294px;top:405px"><div class="req-icon" role="img" aria-label="Containment icon"></div><span class="req-num">5</span><p class="req-text">Plan in place to trigger targeted or full-scale containment in case of sudden outbreaks</p></div>
    <div class="req" style="left:294px;top:474px"><div class="req-icon" role="img" aria-label="Tracking icon"></div><span class="req-num">6</span><p class="req-text">Ability to track and trace infected patients and contacts on a live basis and across the country and ability to react quickly to any unusual trends or outbreaks.</p></div>

    <div class="req" style="left:542px;top:335px"><div class="req-icon" role="img" aria-label="Thermometer icon"></div><span class="req-num">7</span><p class="req-text">Mandatory daily checks of body temperature for everyone at the workplace or entering public areas.</p></div>
    <div class="req" style="left:542px;top:405px"><div class="req-icon" role="img" aria-label="Hand sanitizer icon"></div><span class="req-num">8</span><p class="req-text">Mandatory sanitation in all places - use of disinfection available on a large scale.</p></div>
    <div class="req" style="left:542px;top:474px"><div class="req-icon" role="img" aria-label="Face mask icon"></div><span class="req-num">3</span><p class="req-text tight">Mandatory use of masks (at least surgical grade) for everyone in all public areas and at work. Mandatory use of N95, or equivalent, masks for all healthcare front workers and for all government agencies and authorities that are involved in overseeing the containment activities.</p></div>

    <div class="plan-band">PHASED COVID-19 LOCKDOWN EXIT STRATEGY PLAN</div>
    <p class="plan-lead">To enter this stage, additional to the general requirements, the Effective Reproduction Number (Rt) must be less than 1 and the death rate at less than 3%.<strong>The economy and social activities can resume in this sequence:</strong></p>

    <section class="plan-box">
      <div class="step left" style="top:14px"><div class="step-icon" role="img" aria-label="Elderly person icon"></div><p class="step-text" style="top:10px">Elderly (60+ years old) nd vulnerable individuals should continue to self-isolate.</p></div>
      <div class="step left" style="top:102px"><div class="step-icon" role="img" aria-label="Work from home icon"></div><p class="step-text" style="top:12px">Work from home should continue whenever and as much as possible.</p></div>
      <div class="step left" style="top:176px"><div class="step-icon" role="img" aria-label="No air travel icon"></div><p class="step-text" style="top:0">Non-essential travel should be minimized between cities and regions (and within cities and regions where covid-19 infections are still a risk)</p></div>
      <div class="step left" style="top:264px"><div class="step-icon" role="img" aria-label="Factory icon"></div><p class="step-text" style="top:0">Large businesses (300 people and more, manufacturing, services, etc.) can reopen progressively. Common areas should remain closed (cafeteria, restaurant, gym, meeting rooms of no more than 5 people).</p></div>
      <div class="step left" style="top:378px"><div class="step-icon" role="img" aria-label="Cafe icon"></div><p class="step-text" style="top:0">Coffee &amp; restaurants can reopen but must operate at 30% capacity as well and comply with social distancing. Clients must wear as much as possible their masks if they are not consuming food/coffee. Clients should avoid to talking to each other with masks off.</p></div>
      <div class="step left" style="top:522px"><div class="step-icon" role="img" aria-label="Closed stadium icon"></div><p class="step-text" style="top:0">Large scale events (cinema, theaters, sport, business conferences, etc.) should remain closed or operate virtually. Sport events can resume but without spectators. Athletes and the staff surrounding them should be tested, disinfectants should be available and masks used as much as reasonably possible.</p></div>
      <div class="step left" style="top:680px"><div class="step-icon" role="img" aria-label="Closed school icon"></div><p class="step-text" style="top:6px">All schools should remain closed. On-line courses should continue be the preferred method for education.</p></div>

      <div class="step right" style="top:14px"><div class="step-icon" role="img" aria-label="No gatherings icon"></div><p class="step-text" style="top:6px">No more than 5 people maximum gathering at a time in public areas and at work.</p></div>
      <div class="step right" style="top:96px"><div class="step-icon" role="img" aria-label="Two metre distancing icon"></div><p class="step-text" style="top:0">Social distancing should continue to be re-enforced in public areas, at work and in all areas reopened.</p></div>
      <div class="step right" style="top:180px"><div class="step-icon" role="img" aria-label="Small shop icon"></div><p class="step-text" style="top:4px">Small businesses (300 people and less) can reopen as well with the same conditions as large businesses.</p></div>
      <div class="step right" style="top:264px"><div class="step-icon" role="img" aria-label="Hotel icon"></div><p class="step-text" style="top:0">Hotels &amp; tourism (museums, etc.) can reopen but must operate at 30% or less capacity. All common areas (restaurants, gyms, swimming pools, conference rooms, etc.) should remain closed.</p></div>
      <div class="step right" style="top:378px"><div class="step-icon" role="img" aria-label="Religious building icon"></div><p class="step-text" style="top:0">Religious sites can reopen with a maximum capacity of 30% or less. Social distancing and wearing masks is mandatory. Religious sites should organize (volunteers can help) to check body temperature of everyone accessing the site and provide disinfectant at entry.</p></div>
      <div class="step right" style="top:522px"><div class="step-icon" role="img" aria-label="Pharmacy icon"></div><p class="step-text" style="top:0">Pharmacies will continue to be open. However, they must make available disinfectant for use by clients and will continue to comply with social distancing. Pharmacies should limit the number of client/patient in their stores not to exceed 30% of the standard capacity.</p></div>
      <div class="step right" style="top:674px"><div class="step-icon" role="img" aria-label="Shop icon"></div><p class="step-text" style="top:0">Commercial shops can reopen. Shops should control the flow of people in their facilities not to exceed 30% at a time of standard capacity. Shops should provide disinfectant and temperature control at entry.</p></div>

      <div class="step transport left" style="top:780px"><div class="step-icon" role="img" aria-label="Delivery truck icon" style="top:18px"></div><p class="step-text" style="top:0">Transportation (buses, taxis, airlines) will resume progressively. No air travels permitted in and out of Covid-19 known hotspots, locally or internationally. Entry to country should be limited and strictly controlled. All landing passengers and visitors regardless of the country of origin should be tested for Covid-19 at arrival. All passengers and visitors will undergo a temperature check at arrival. No more than 3 people at a time in a taxi/Ridely including the driver. All passengers wearing masks. Buses should operate with no more than 30% customer's capacity per bus.</p></div>
    </section>

    <footer class="footer-band">DON’T HAVE TO GO OUTSIDE ? &nbsp; PLEASE STAY AT HOME!</footer>
  </article>
</div>
</body>
</html>
```